Brindle Barks Chews Pouch Design

I want a pouch design for my yak cheese dog chews. My competitor is kindly tail, see attached. I want something minimalist like that where you see that there is only 3 ingredients, Yak milk, lime juice, Himalayan salt. I want it to say 100% natural 100% organic on it. Also odor free. There has to be a big see through window on it so you can see the products inside. Here is my logo and my competitor package. The package is 13cm x 17cm x 5cm. I have 5 sizes of bags to create but same image design
Updates

Target Market(s)

Pet owners

Industry/Entity Type

Dog products

Requirements
Must have
• « SMALL » « MIN NET WT 200 g / 5 PCS » and its important the 3 ingredients mentioned and 100% natural and organic must be very visible however the window must be big
Should not have
• The ingredients in the back

```html
<!DOCTYPE html>
<html lang="en">
<head>
<meta charset="utf-8">
<title>Brindle Barks Yak Cheese Dog Chews – Pouch</title>
<link rel="stylesheet" href="https://fonts.googleapis.com/css2?family=Patrick+Hand+SC&family=Open+Sans:ital,wght@1,800&display=swap">
<style>
  :root {
    --backdrop: #073c48;
    --top-orange: #f7a531;
    --cream: #fbf6dc;
    --maroon: #6b2630;
    --teal: #1a8aa2;
    --teal-deep: #137489;
    --chew-light: #f2a545;
    --chew-dark: #c9631e;
    --white: #ffffff;
  }
  html, body {
    margin: 0;
    width: 1200px;
    height: 1042px;
    overflow: hidden;
    background: var(--backdrop);
  }
  .pouch {
    position: absolute;
    left: 330px;
    top: 168px;
    width: 540px;
    height: 706px;
    display: block;
  }
  .hand { font-family: "Patrick Hand SC", cursive; }
  .label { font-family: "Open Sans", sans-serif; font-style: italic; font-weight: 800; }
  .title { fill: var(--maroon); font-size: 54px; }
  .claim {
    fill: var(--white);
    stroke: var(--maroon);
    stroke-width: 5px;
    paint-order: stroke;
    stroke-linejoin: round;
  }
  .brand { fill: var(--maroon); font-size: 30px; }
  .odor { fill: var(--cream); font-size: 22px; }
  .ingredients { fill: var(--maroon); font-size: 30px; letter-spacing: 1px; }
  .small-label { fill: var(--maroon); font-size: 11px; }
</style>
</head>
<body>
<svg class="pouch" viewBox="0 0 540 706" xmlns="http://www.w3.org/2000/svg" aria-label="Brindle Barks yak cheese dog chews pouch front">
  <defs>
    <linearGradient id="chewFill" x1="0" y1="0" x2="1" y2="0">
      <stop offset="0" stop-color="var(--chew-dark)"/>
      <stop offset="0.3" stop-color="var(--chew-light)"/>
      <stop offset="0.55" stop-color="var(--chew-dark)"/>
      <stop offset="0.8" stop-color="var(--chew-light)"/>
      <stop offset="1" stop-color="var(--chew-dark)"/>
    </linearGradient>
    <path id="ingredientCurve" d="M30 585 C140 640 300 560 525 570"/>
  </defs>

  <!-- pouch body -->
  <rect class="pouch-body" x="0" y="0" width="540" height="706" fill="var(--cream)"/>

  <!-- top colour band -->
  <path class="top-band" d="M0 0 H540 V60 C460 70 400 95 330 90 C240 85 150 150 0 175 Z" fill="var(--top-orange)"/>

  <!-- hang slot -->
  <rect class="hang-slot" x="230" y="28" width="66" height="14" rx="7" fill="var(--backdrop)"/>
  <rect x="258" y="14" width="10" height="20" rx="5" fill="var(--backdrop)"/>

  <!-- odor free tab -->
  <path class="odor-tab" d="M420 0 H480 V102 Q480 108 474 108 H426 Q420 108 420 102 Z" fill="var(--maroon)"/>
  <text class="hand odor" x="450" y="65" text-anchor="middle">ODOR</text>
  <text class="hand odor" x="450" y="90" text-anchor="middle">FREE</text>

  <!-- brand mark -->
  <circle class="brand-dot" cx="105" cy="115" r="48" fill="var(--maroon)"/>
  <text class="hand brand" x="105" y="200" text-anchor="middle">Brindle Barks</text>

  <!-- product window -->
  <path class="window" role="img" aria-label="See-through window showing yak cheese chew sticks"
        d="M30 268 C150 252 320 258 512 238 V470 C380 500 240 520 30 565 Z" fill="url(#chewFill)"/>

  <!-- title -->
  <g transform="rotate(-8 370 170)">
    <text class="hand title" x="228" y="178">YAK CHEESE</text>
    <text class="hand title" x="228" y="238">DOG CHEWS</text>
  </g>

  <!-- claims -->
  <text class="hand claim" x="48" y="380" font-size="92">100%</text>
  <text class="hand claim" x="48" y="458" font-size="64">NATURAL</text>
  <text class="hand claim" x="48" y="532" font-size="64">ORGANIC</text>
  <text class="hand claim" x="286" y="498" font-size="40">&amp;</text>

  <!-- bottom band -->
  <path class="bottom-band" d="M0 645 C150 650 330 580 540 560 V706 H0 Z" fill="var(--teal)"/>
  <path d="M0 690 C180 690 360 640 540 620 V706 H0 Z" fill="var(--teal-deep)" opacity="0.5"/>

  <!-- ingredients -->
  <text class="hand ingredients">
    <textPath href="#ingredientCurve">YAK MILK • LIME JUICE • HIMALAYAN SALT</textPath>
  </text>

  <!-- weight / count / size -->
  <rect x="255" y="638" width="110" height="20" rx="3" fill="var(--cream)"/>
  <text class="label small-label" x="310" y="652" text-anchor="middle">MIN NET WT 200g</text>
  <circle cx="405" cy="635" r="34" fill="var(--white)" stroke="var(--maroon)" stroke-width="3"/>
  <text class="label" x="405" y="640" text-anchor="middle" fill="var(--maroon)" font-size="30">5</text>
  <text class="label small-label" x="405" y="657" text-anchor="middle">PCS</text>
  <rect x="442" y="618" width="52" height="20" rx="3" fill="var(--cream)"/>
  <text class="label small-label" x="468" y="632" text-anchor="middle">SMALL</text>
</svg>
</body>
</html>
```